Business software developers new website

We need to redesign our website. Our current website is http://www.plovencast.example/index.html, which is outdated and needs a new look. We moved out from web design and have concentrated more on the back end of the systems, for example, system support and security and cloud-based applications. Our major clients include both private and government sectors. We would like to see some designs that are all in one page, simple and clean. Prefer illustrator or obstructed images instead of real-life photos. Must look futuristic yet friendly. Attached the new logo for your references and good luck.

Target Market(s)

Medium to big company for their IT or data management. Either improve or upgrade their current system.

Industry/Entity Type

Business Software

Number of Pages Required

1 page

Colors

Designer to choose colors to be used in the design.

Requirements
Must have
• Simple and clean. Individual assets must be provided in the correct size and format(png or jpeg). Prefer Goggle fonts. Even though the logo color is red, grey and black, still prefer some modern colors that go well with red. When design, must consider the possibility to convert it into responsive.
Nice to have
• White background
Should not have
• real life photos, no slider

```html
<!DOCTYPE html>
<html lang="en">
<head>
<meta charset="utf-8">
<title>Plovencast – Business Software Developers</title>
<link href="https://fonts.googleapis.com/css2?family=Roboto:wght@400;500;700&family=Lato:ital,wght@0,400;0,700;1,400&display=swap" rel="stylesheet">
<style>
:root{
  --navy:#173b63;
  --red:#e31b36;
  --ink:#1f2a37;
  --text:#666d76;
  --bg-soft:#f2f4f8;
  --line:#c9ced6;
  --white:#ffffff;
}
*{margin:0;padding:0;box-sizing:border-box}
html,body{width:1200px;height:4850px;overflow:hidden}
body{position:relative;background:var(--white);font-family:"Lato",sans-serif;color:var(--text)}
.abs{position:absolute}
.backdrop{position:absolute;left:0;top:0;width:1200px;height:4850px}
.brand{left:113px;top:30px;font-family:"Roboto",sans-serif;font-size:42px;color:var(--white);letter-spacing:-0.5px;display:flex;align-items:center;gap:10px}
.brand-dot{width:12px;height:12px;background:var(--white);border-radius:50%}
.nav{top:42px;left:740px;font-family:"Roboto",sans-serif;font-size:16px;color:var(--white)}
.nav a{position:absolute;color:var(--white);text-decoration:none;white-space:nowrap}
.nav a.active{color:var(--red)}
.hero-title{left:111px;top:175px;font-family:"Roboto",sans-serif;font-weight:700;font-size:74px;color:var(--white)}
.hero-sub{left:111px;top:282px;font-size:22px;color:var(--white)}
.btn-red{background:var(--red);color:var(--white);font-family:"Lato",sans-serif;font-weight:700;font-size:16px;display:flex;align-items:center;justify-content:center;letter-spacing:.3px}
.hero-btn{left:111px;top:347px;width:181px;height:53px}
.hero-art{left:509px;top:94px;width:678px;height:594px;border-radius:6px;background:linear-gradient(135deg,#2f8df2 0%,#7ec1ff 50%,#e6f1fd 100%);opacity:.9}
.video-art{left:75px;top:795px;width:525px;height:307px;border-radius:12px;background:linear-gradient(180deg,#1e2125,#2c3136 85%,#d7d9dc 86%,#eceeef)}
.h2{font-family:"Roboto",sans-serif;font-weight:500;color:var(--navy);font-size:42px;white-space:nowrap}
.welcome-title{left:652px;top:788px}
.para{font-size:14px;line-height:28px;color:var(--text)}
.welcome-p1{left:652px;top:866px;width:440px}
.welcome-p2{left:652px;top:1003px;width:440px}
.btn-outline{left:652px;top:1100px;width:136px;height:49px;border:2px solid var(--red);color:var(--red);font-weight:700;font-size:15px;display:flex;align-items:center;justify-content:center;background:var(--white)}
.center{left:0;width:1200px;text-align:center}
.card{background:var(--white);box-shadow:0 1px 6px rgba(0,0,0,.08);text-align:center;width:303px;height:386px}
.card.hover{box-shadow:0 4px 18px rgba(0,0,0,.16)}
.card-icon{margin:50px auto 0;width:124px;height:120px;border-radius:8px;background:linear-gradient(160deg,#e8ecf3 0%,#f6d0d5 100%)}
.card h3{font-family:"Roboto",sans-serif;font-weight:500;font-size:23px;color:var(--ink);margin-top:40px}
.card p{font-size:14px;line-height:28px;color:var(--text);padding:0 22px;margin-top:14px}
.card .more{font-size:15px;font-weight:700;color:var(--red);margin-top:14px}
.client{width:330px;text-align:center}
.client-name{height:132px;display:flex;align-items:center;justify-content:center;gap:12px;font-family:"Roboto",sans-serif;font-weight:700;font-size:30px;color:var(--navy)}
.client-mark{width:22px;height:22px;border-radius:50%;background:var(--red)}
.client p{font-size:14px;line-height:27px;margin-top:24px}
.quote-card{width:307px;height:234px;background:var(--white);border-top:4px solid var(--navy);box-shadow:0 1px 6px rgba(0,0,0,.08);text-align:center;padding:40px 22px 0}
.quote-card.accent{border-top-color:var(--red)}
.quote-card q{display:block;font-style:italic;font-size:13.5px;line-height:25px;color:var(--text);quotes:"“" "”"}
.quote-card .who{font-weight:700;font-size:18px;color:var(--ink);margin-top:14px}
.quote-card .role{font-style:italic;font-size:13.5px;color:#2a62a8;margin-top:6px}
.h3{font-weight:700;font-size:21px;color:var(--ink)}
.field{border:1px solid var(--line);border-radius:6px;background:var(--white);font-size:13px;color:#555;padding-left:16px;display:flex;align-items:center}
.field.area{align-items:flex-start;padding-top:15px}
.submit{left:608px;top:4648px;width:106px;height:41px;border-radius:21px;font-size:14px}
.info-row{left:778px;display:flex;align-items:flex-start;gap:16px;font-size:13.5px;line-height:25px;color:var(--text)}
.info-icon{width:34px;height:34px;border-radius:50%;border:1px solid var(--line);flex:none;display:flex;align-items:center;justify-content:center}
.social{top:4669px;width:34px;height:34px;border-radius:50%;border:1px solid var(--line);display:flex;align-items:center;justify-content:center;font-size:9px;font-weight:700;color:var(--red)}
.footer-line{left:111px;top:4744px;width:969px;height:1px;background:#d5d9df}
.copy{top:4784px;font-size:13px;color:var(--text)}
</style>
</head>
<body>

<svg class="backdrop" viewBox="0 0 1200 4850" aria-hidden="true">
  <polygon points="0,1583 1200,1130 1200,4050 0,4250" fill="var(--bg-soft)"/>
  <polygon points="0,2890 1200,2430 1200,2560 0,3020" fill="#f8f9fb"/>
  <polygon points="0,3600 1200,3150 1200,3280 0,3730" fill="#f8f9fb"/>
  <polygon points="0,0 1200,0 1200,115 0,688" fill="var(--navy)"/>
</svg>

<div class="abs brand"><span>plovencast</span><span class="brand-dot"></span><span>net</span></div>
<nav class="abs nav">
  <a class="active" href="#" style="left:0">Home</a>
  <a href="#" style="left:74px">Servies</a>
  <a href="#" style="left:160px">Clients</a>
  <a href="#" style="left:243px">Contact</a>
  <svg style="position:absolute;left:335px;top:2px" width="16" height="16" viewBox="0 0 16 16"><circle cx="6.5" cy="6.5" r="5" fill="none" stroke="#fff" stroke-width="2"/><line x1="10.5" y1="10.5" x2="15" y2="15" stroke="#fff" stroke-width="2.4"/></svg>
</nav>
<h1 class="abs hero-title">Plovencast</h1>
<p class="abs hero-sub">We are business software developers.</p>
<div class="abs btn-red hero-btn">GET MORE INFO</div>
<div class="abs hero-art" role="img" aria-label="Isometric illustration of a computer with code windows, gears and technology labels"></div>

<div class="abs video-art" role="img" aria-label="Laptop showing a code editor with a play button for a video"></div>
<h2 class="abs h2 welcome-title">Welcome to Plovencast</h2>
<p class="abs para welcome-p1">We have provided web design, graphic design and application development solutions for a wide variety of industries. We are known for the quality of our work, affordable rates and our individual approach to each customer.</p>
<p class="abs para welcome-p2">Our company offers a wide variety of professional web solution and all this at very competitive prices!</p>
<div class="abs btn-outline">READ MORE</div>

<h2 class="abs h2 center" style="top:1495px">Our Services</h2>
<div class="abs card" style="left:111px;top:1615px"><div class="card-icon" role="img" aria-label="Web design icon"></div><h3>Web Design</h3><p>Your website needs the 'wow' factor to meet you're audiences needs. Without this, you won't entice visitors</p></div>
<div class="abs card hover" style="left:448px;top:1615px"><div class="card-icon" role="img" aria-label="Software development icon"></div><h3>Software Development</h3><p>We build robust, reliable websites – and make sure they stay that way. We cover all your online needs,</p><div class="more">READ MORE</div></div>
<div class="abs card" style="left:786px;top:1615px"><div class="card-icon" role="img" aria-label="Marketing icon"></div><h3>Marketing</h3><p>Beside using the latest techniques to improve your Search Engine Ranking and make your site visible</p></div>
<div class="abs card" style="left:111px;top:2044px"><div class="card-icon" role="img" aria-label="Programming icon"></div><h3>Programming</h3><p>We aim to deliver the best user experience to our customers without sacrificing security, performance</p></div>
<div class="abs card" style="left:448px;top:2044px"><div class="card-icon" role="img" aria-label="Web standards icon"></div><h3>W3C Compliant</h3><p>All of our sites are W3C compliant, so you never have to worry about incompatiblities between browsers.</p></div>
<div class="abs card" style="left:786px;top:2044px"><div class="card-icon" role="img" aria-label="Hosting icon"></div><h3>Hosting Solutions</h3><p>We offer competitive hosting solutions with all of our projects so you never have to worry about finding</p></div>

<h2 class="abs h2 center" style="top:2810px">Our Clients</h2>
<div class="abs client" style="left:80px;top:2911px"><div class="client-name"><span class="client-mark"></span>Quorvane</div><p>International currency matching system that allows expat Australians to transfer money between countries</p></div>
<div class="abs client" style="left:434px;top:2911px"><div class="client-name"><span class="client-mark"></span>CRSO</div><p>The Clinical Research Society of Oceania held its inaugural Annual Scientific Meeting in Canberra in 2000, and it has</p></div>
<div class="abs client" style="left:777px;top:2911px"><div class="client-name"><span class="client-mark"></span>Marcellos</div><p>Paul Verrano has been welcoming friends to Marcellos for over 35 years. Generation after generation of tourists and locals</p></div>

<h2 class="abs h2 center" style="top:3495px">Testimonials</h2>
<div class="abs quote-card" style="left:98px;top:3600px"><q>Nam libero tempore, cum soluta nobis est eligendi optio cumque nihil impedit quo minus id quod maxime placeat facere possi mus, omqmnis volup</q><div class="who">Lucien Fabre</div><div class="role">Propriétaire - Fabre Studio</div></div>
<div class="abs quote-card accent" style="left:447px;top:3600px"><q>Nam libero tempore, cum soluta nobis est eligendi optio cumque nihil impedit quo minus id quod maxime placeat facere possi mus, omqmnis volup</q><div class="who">Remy Castel</div><div class="role">Propriétaire - Fabre Studio</div></div>
<div class="abs quote-card" style="left:795px;top:3600px"><q>Nam libero tempore, cum soluta nobis est eligendi optio cumque nihil impedit quo minus id quod maxime placeat facere possi mus, omqmnis volup</q><div class="who">Olivier Marchand</div><div class="role">Propriétaire - Fabre Studio</div></div>

<h2 class="abs h2 center" style="top:4252px">Contact Us</h2>
<h3 class="abs h3" style="left:109px;top:4362px">Contact form</h3>
<div class="abs field" style="left:111px;top:4422px;width:296px;height:45px">Name :</div>
<div class="abs field" style="left:416px;top:4422px;width:298px;height:45px">Phone no :</div>
<div class="abs field" style="left:111px;top:4488px;width:603px;height:45px">Email :</div>
<div class="abs field area" style="left:111px;top:4546px;width:603px;height:81px">Message :</div>
<div class="abs btn-red submit">SUBMIT</div>

<h3 class="abs h3" style="left:778px;top:4362px">Contact Information</h3>
<div class="abs info-row" style="top:4418px"><span class="info-icon"><svg width="14" height="16" viewBox="0 0 14 16"><path d="M7 1a5 5 0 0 0-5 5c0 4 5 9 5 9s5-5 5-9a5 5 0 0 0-5-5z" fill="var(--red)"/><circle cx="7" cy="6" r="1.8" fill="#fff"/></svg></span><span>418 Harbourview Ave, Suite 12<br>Eastport, Calder 40921</span></div>
<div class="abs info-row" style="top:4484px"><span class="info-icon"><svg width="14" height="14" viewBox="0 0 14 14"><path d="M3 1l2.5 3-1.5 1.5a8 8 0 0 0 4.5 4.5L10 8.5 13 11l-1.5 2C6 13 1 8 1 2.5z" fill="var(--red)"/></svg></span><span style="padding-top:4px">+00 5 0123 4567</span></div>
<div class="abs info-row" style="top:4544px"><span class="info-icon"><svg width="14" height="10" viewBox="0 0 14 10"><rect width="14" height="10" rx="1.5" fill="var(--red)"/><path d="M1 1l6 5 6-5" fill="none" stroke="#fff" stroke-width="1.3"/></svg></span><span style="padding-top:4px">info@plovencast.example</span></div>

<h3 class="abs h3" style="left:778px;top:4622px">Social Media</h3>
<div class="abs social" style="left:776px">Bevo</div>
<div class="abs social" style="left:823px">Tisk</div>
<div class="abs social" style="left:868px">Orna</div>

<div class="abs footer-line"></div>
<p class="abs copy center">Copyright © 2019, Plovencast. All rights reserved.</p>
<svg class="abs" style="left:1062px;top:4780px" width="28" height="16" viewBox="0 0 28 16" aria-label="Back to top"><polyline points="2,14 14,3 26,14" fill="none" stroke="#b9bec6" stroke-width="2.5"/></svg>

</body>
</html>
```